A private security company called "Tavron Security Services Ltd"

Hello everybody,

We need a web page for a company based in NZ. It is mainly an informative website so it would be wonderful if the designer puts their absolute best into making it a website that I would really appreciate. The website needs to show professionalism and also needs to make our web surfers find the information they need in a click. the company's colour is black and silver, and if those two colours could be integrated into the website it would be absolutely lovely. Please do contact me for any information.

Sincerely,
Dorian Vaskel

Industry/Entity Type

Security

```html
<!DOCTYPE html>
<html lang="en">
<head>
<meta charset="utf-8">
<title>Tavron Security Services Ltd</title>
<link href="https://fonts.googleapis.com/css2?family=Oswald:wght@300;400&family=Arimo:wght@400;700&display=swap" rel="stylesheet">
<style>
:root{
  --ink:#111;
  --text:#333;
  --muted:#9a9a9a;
  --silver:#e6e6e6;
  --silver-dark:#cfcfcf;
  --hero-top:#5b5b5b;
  --hero-bottom:#222;
  --footer-top:#444;
  --footer-bottom:#2b2b2b;
  --footer-bar:#262626;
  --white:#fff;
  --head:'Oswald',sans-serif;
  --body:'Arimo',Arial,sans-serif;
}
*{margin:0;padding:0;box-sizing:border-box}
html,body{width:1200px;height:2619px;overflow:hidden}
body{font-family:var(--body);color:var(--text);background:var(--white);position:relative}

/* header */
.site-header{position:absolute;left:0;top:0;width:1200px;height:159px;background:linear-gradient(#fbfbfb,#e9e9e9)}
.brand{position:absolute;left:157px;top:30px;display:flex;align-items:center;gap:12px;font-family:var(--head);font-weight:400;color:var(--ink)}
.brand-mark{width:44px;height:44px;border-radius:50%;background:var(--ink)}
.brand-name{font-size:30px;line-height:30px;letter-spacing:2px}
.brand-sub{font-size:13px;line-height:16px;letter-spacing:.5px}
.social{position:absolute;display:flex;gap:9px}
.social span{width:30px;height:30px;border-radius:50%;background:#b3b3b3;display:block}
.social.top{left:933px;top:32px}
.main-nav{position:absolute;left:408px;top:98px;display:flex;gap:33px;font-size:13px;color:#222}

/* hero */
.hero{position:absolute;left:0;top:159px;width:1200px;height:515px;background:radial-gradient(ellipse at 40% 30%,var(--hero-top),#3a3a3a 55%,var(--hero-bottom))}
.hero-photo{position:absolute;left:690px;top:20px;width:330px;height:495px;background:linear-gradient(#2a2a2a,#0d0d0d);border-radius:80px 80px 0 0}
.hero-title{position:absolute;left:200px;top:222px;font-family:var(--head);font-weight:300;font-size:33px;line-height:46px;color:var(--white)}
.hero-title b{font-weight:400;font-size:40px}
.hero-arrow{position:absolute;top:233px;width:50px;height:50px;border-radius:50%;background:rgba(120,120,120,.8)}
.hero-arrow svg{display:block}
.hero-arrow.prev{left:104px}.hero-arrow.next{left:1046px}

/* solutions */
.solution{position:absolute;top:724px;width:260px;text-align:center}
.solution-photo{width:182px;height:182px;margin:0 auto;border-radius:50%;border:9px solid #e8e8e8;box-shadow:0 2px 6px rgba(0,0,0,.2)}
.solution h3{font-family:var(--head);font-weight:400;font-size:20px;color:var(--ink);margin-top:24px}
.solution p{font-size:12px;line-height:16px;color:var(--muted);margin:14px 14px 0}
.btn{display:inline-block;border:1px solid #bdbdbd;border-radius:3px;background:linear-gradient(#fff,#e3e3e3);color:#222;font-size:12px;line-height:28px;padding:0 26px}
.solution .btn{margin-top:22px}

/* services */
.services{position:absolute;left:0;top:1133px;width:1200px;height:585px;background:linear-gradient(#f4f4f4,#dedede)}
.services h2{position:absolute;left:157px;top:30px;font-family:var(--head);font-weight:400;font-size:22px;color:var(--ink)}
.service-list{position:absolute;left:160px;top:88px;list-style:none;font-size:12px;color:#555}
.service-list li{height:37px;display:flex;align-items:center;gap:14px}
.service-list li::before{content:"";width:13px;height:13px;border-radius:50%;background:#fff;box-shadow:0 1px 2px rgba(0,0,0,.25)}
.custom-box{position:absolute;left:157px;top:424px;width:212px;height:150px;background:linear-gradient(90deg,#6a6a6a,#bdbdbd);font-family:var(--head);font-weight:300;color:var(--white);padding:12px 14px;font-size:22px;line-height:30px;text-transform:uppercase}
.custom-box small{display:block;font-size:17px;margin-top:4px}
.service-grid{position:absolute;left:376px;top:0;display:flex}
.service-col{width:223px;border-left:1px solid #d0d0d0}
.service-col:last-child{border-right:1px solid #d0d0d0}
.service-card{position:relative;border-bottom:1px solid #d0d0d0;padding:30px 16px 0}
.service-card:last-child{border-bottom:none}
.service-card h3{font-family:var(--head);font-weight:400;font-size:17px;color:var(--ink);margin-bottom:24px}
.service-card p{font-size:11px;line-height:15px;color:#666;margin-bottom:12px}
.service-card .btn{position:absolute;right:16px;bottom:14px;font-size:11px;line-height:24px;padding:0 10px}

/* testimonials */
.clients-title{position:absolute;left:0;top:1772px;width:1200px;text-align:center;font-family:var(--head);font-weight:400;font-size:38px;color:var(--ink)}
.quote{position:absolute;top:1891px;width:277px;height:112px;background:linear-gradient(#fff,#ececec);box-shadow:0 1px 3px rgba(0,0,0,.15);border-bottom:4px solid #222;padding:18px 14px;font-size:11px;line-height:13px;color:#555}
.quote::after{content:"";position:absolute;left:30px;bottom:-14px;border:10px solid transparent;border-top-color:#222;border-bottom:none}
.client{position:absolute;top:2040px;display:flex;align-items:center;gap:18px;font-family:var(--head);font-weight:400;font-size:17px;color:var(--ink)}
.avatar{width:36px;height:36px;border-radius:50%;background:#c9c9c9}

/* footer */
.site-footer{position:absolute;left:0;top:2138px;width:1200px;height:481px;background:linear-gradient(var(--footer-top),var(--footer-bottom));color:#a8a8a8}
.site-footer h2{position:absolute;top:58px;font-family:var(--head);font-weight:300;font-size:27px;color:var(--white)}
.about-text{position:absolute;left:157px;top:124px;width:305px;font-size:12px;line-height:15px}
.about-text p+p{margin-top:12px}
.quick-links{position:absolute;left:541px;top:124px;list-style:none;font-size:11.5px;text-transform:uppercase}
.quick-links li{height:31.5px;display:flex;gap:12px}
.quick-links li::before{content:"›";color:#fff;font-size:16px;line-height:13px}
.newsletter-note{position:absolute;left:768px;top:126px;width:280px;font-size:11px;line-height:15px}
.field{position:absolute;left:768px;width:275px;height:34px;background:#5c5c5c;border:1px solid #6d6d6d;color:#ccc;font-size:12px;line-height:32px;padding-left:20px}
.signup{position:absolute;left:768px;top:292px;width:142px;height:36px;background:#fff;border-radius:2px;color:#111;font-size:12px;line-height:36px;text-align:center}
.footer-bar{position:absolute;left:0;bottom:0;width:1200px;height:82px;background:var(--footer-bar);border-top:1px solid #333}
.copyright{position:absolute;left:157px;top:36px;font-size:12px;color:#999}
.social.bottom{left:933px;top:25px}
</style>
</head>
<body>

<header class="site-header">
  <div class="brand">
    <span class="brand-mark"></span>
    <div><div class="brand-name">TAVRON</div><div class="brand-sub">Security Services Ltd.</div></div>
  </div>
  <div class="social top"><span></span><span></span><span></span></div>
  <nav class="main-nav"><span>HOME</span><span>OUR SERVICES</span><span>ABOUT</span><span>LOCATIONS</span><span>NEWS</span><span>CAREERS</span><span>CONTACT US</span></nav>
</header>

<section class="hero">
  <div class="hero-photo" role="img" aria-label="Security guard in black uniform and cap seen from behind"></div>
  <p class="hero-title"><b>Lorem Ipsum</b> is simply dummy text of<br>the printing and typesetting industry.</p>
  <div class="hero-arrow prev"><svg width="50" height="50"><path d="M29 15 L20 25 L29 35" stroke="#fff" stroke-width="2" fill="none"/></svg></div>
  <div class="hero-arrow next"><svg width="50" height="50"><path d="M21 15 L30 25 L21 35" stroke="#fff" stroke-width="2" fill="none"/></svg></div>
</section>

<section class="solutions">
  <div class="solution" style="left:143px">
    <div class="solution-photo" role="img" aria-label="Woman using a home alarm keypad" style="background:linear-gradient(135deg,#8a6a55,#d8c8b8)"></div>
    <h3>Residential Solutions</h3>
    <p>Lorem ipsum dolor sit amet, consec tetur adipiscing elit. Donec vitae pharetra nunc. Aliquam condimentum neque nibh, ac vestibulum</p>
    <span class="btn">Read More</span>
  </div>
  <div class="solution" style="left:469px">
    <div class="solution-photo" role="img" aria-label="Security officer in front of office towers" style="background:linear-gradient(135deg,#9fb4c8,#2b2b2b)"></div>
    <h3>Commercial Solutions</h3>
    <p>Lorem ipsum dolor sit amet, consec tetur adipiscing elit. Donec vitae pharetra nunc. Aliquam condimentum neque nibh, ac vestibulum</p>
    <span class="btn">Read More</span>
  </div>
  <div class="solution" style="left:795px">
    <div class="solution-photo" role="img" aria-label="Operators watching a wall of surveillance monitors" style="background:linear-gradient(135deg,#3a6a9a,#1a2a3a)"></div>
    <h3>Technology Solutions</h3>
    <p>Lorem ipsum dolor sit amet, consec tetur adipiscing elit. Donec vitae pharetra nunc. Aliquam condimentum neque nibh, ac vestibulum</p>
    <span class="btn">Read More</span>
  </div>
</section>

<section class="services">
  <h2>Services</h2>
  <ul class="service-list">
    <li>Access Control</li><li>Video Surveillance</li><li>Intrusion Detection</li><li>Locking Solutions</li><li>Key Control</li><li>Security Guard</li><li>Security Patrol</li><li>Alarm Monitoring</li><li>Executive Protection</li>
  </ul>
  <div class="custom-box" role="img" aria-label="Technician installing a door lock">Custom<br>Options<br>Available<small>Call 987-650-314</small></div>
  <div class="service-grid">
    <div class="service-col">
      <div class="service-card" style="height:275px"><h3>Access Control</h3>
        <p>Lorem ipsum dolor sit amet, cons ectetuer adipiscing elit, sed diam nonummy nibh euismod tincidunt</p>
        <p>ut laoreet dolore magna aliquam erat volutpat. Ut wisi enim ad minim veniam, quis nostrud exerci tation ullamcorper suscipit lobortis nisl.</p>
        <span class="btn">Read More</span></div>
      <div class="service-card" style="height:310px"><h3>Security Guard</h3>
        <p>Lorem ipsum dolor sit amet, cons ectetuer adipiscing elit, sed diam nonummy nibh euismod tincidunt ut laoreet dolore magna aliquam erat volutpat. Ut wisi enim ad mini m veniam, quis nostrud exerci tati on ullamcorper suscipit lobortis nisl ut aliquip ex ea commodo consequat.</p>
        <span class="btn">Read More</span></div>
    </div>
    <div class="service-col">
      <div class="service-card" style="height:295px"><h3>Video Surveillance</h3>
        <p>Duis autem vel eum iriure dolor in hendrerit in vulputate velit esse molestie consequat.</p>
        <p>Vel illum dolore eu feugiat nulla facilisis at vero eros et accumsan et iusto odio dignissim qui blandit praesent luptatum zzril delenit augue duis dolore te feugait nulla facilisi.</p>
        <span class="btn">Read More</span></div>
      <div class="service-card" style="height:290px"><h3>Alarm Monitoring</h3>
        <p>Duis autem vel eum iriure dolor in hendrerit in vulputate velit esse molestie consequat, vel illum dolore eu feugiat nulla facilisis at vero eros et accumsan et iusto odio dignissim qui blandit praesent luptatum zzril delenit augue duis dolore.</p>
        <span class="btn">Read More</span></div>
    </div>
    <div class="service-col">
      <div class="service-card" style="height:262px"><h3>Key Control</h3>
        <p>Ut wisi enim ad minim veniam, quis nostrud exerci tation ullamcorper suscipit lobortis nisl ut aliquip ex ea commodo consequat. Duis autem vel eum iriure dolor in hendrerit in vulputate velit.</p>
        <span class="btn">Read More</span></div>
      <div class="service-card" style="height:323px"><h3>Executive Protection</h3>
        <p>Lorem ipsum dolor sit amet, cons ectetuer adipiscing elit, sed diam nonummy nibh euismod tincidunt ut laoreet dolore magna aliquam erat volutpat. Ut wisi enim ad mini m veniam, quis nostrud exerci tati on ullamcorper suscipit lobortis nisl ut aliquip ex ea commodo consequat.</p>
        <span class="btn">Read More</span></div>
    </div>
  </div>
</section>

<h2 class="clients-title">What Our Clients Says</h2>
<div class="quote" style="left:157px">Lorem ipsum dolor sit amet, cons ectetuer adipiscing elit, sed diam nonummy nibh euismod tincidunt ut laoreet dolore magna aliquam erat volutpat. Ut wisi enim ad minim veniam, quis nostrud exerci tation ullamcorper suscipit lobortis nisl ut aliquip ex ea commodo consequat.</div>
<div class="quote" style="left:464px">Lorem ipsum dolor sit amet, cons ectetuer adipiscing elit, sed diam nonummy nibh euismod tincidunt ut laoreet dolore magna aliquam erat volutpat. Ut wisi enim ad minim veniam, quis nostrud exerci tation ullamcorper suscipit lobortis nisl ut aliquip ex ea commodo consequat.</div>
<div class="quote" style="left:766px">Lorem ipsum dolor sit amet, cons ectetuer adipiscing elit, sed diam nonummy nibh euismod tincidunt ut laoreet dolore magna aliquam erat volutpat. Ut wisi enim ad minim veniam, quis nostrud exerci tation ullamcorper suscipit lobortis nisl ut aliquip ex ea commodo consequat.</div>
<div class="client" style="left:183px"><span class="avatar" role="img" aria-label="Client portrait"></span>Mara Ellington</div>
<div class="client" style="left:487px"><span class="avatar" role="img" aria-label="Client portrait"></span>Callum Reeve</div>
<div class="client" style="left:792px"><span class="avatar" role="img" aria-label="Client portrait"></span>Anton Vereck</div>

<footer class="site-footer">
  <h2 style="left:157px">About us</h2>
  <div class="about-text">
    <p>Lorem ipsum dolor sit amet, consectetur adipiscing elit. Morbi pellentesque iaculis justo eget fermentum. Pellentesque commodo iaculis neque, vitae tincidunt odio pellentesque luctus. Aenean in eros eu magna vestibulum imperdiet pretium nec augue.</p>
    <p>Etiam quis turpis enim. Vestibulum auctor id mauris vulputate consequat. Suspendisse potenti. Cras at imperdiet elit. Integer fringilla tellus non diam condimentum, sed ultricies urna ultricies. Sed cong dui quis dui convallis dictum. Donec malesuada vulputate risus vitae vulputate. Maecenas in congue urna. Sed porttitor bibendum.</p>
  </div>
  <h2 style="left:541px">Quick Links</h2>
  <ul class="quick-links"><li>Home</li><li>Our Services</li><li>About</li><li>Locations</li><li>News</li><li>Careers</li><li>Contact Us</li></ul>
  <h2 style="left:768px">Newsletter Sigup</h2>
  <p class="newsletter-note">Fill the form below and recive our latest offers &amp; updates</p>
  <div class="field" style="top:192px">Your Name</div>
  <div class="field" style="top:238px">Your Email</div>
  <div class="signup">Signup Now!</div>
  <div class="footer-bar">
    <p class="copyright">Copyright © 2014 Tavron Security Service LTD.</p>
    <div class="social bottom"><span></span><span></span><span></span></div>
  </div>
</footer>

</body>
</html>
```